US company marketing to law enforcement needs brochure design

We have created a new logo and now need to update our printed material. What we really need is a "style" or "template" for how our brochures will look in the future. Enclosed is the brochure draft with the old style and logo. Also enclosed is the new logo. As we are marketing to US law enforcement it is important the the brochure design is strong, powerful and that we are looking experienced and trustworthy. However, we also want to look modern in line with the logo update.

Target Market(s)

Law enforcement

Industry/Entity Type

Marketing

```html
<!DOCTYPE html>
<html lang="en">
<head>
<meta charset="utf-8">
<title>Meridian Justice – Brochure Cover</title>
<link rel="stylesheet" href="https://fonts.googleapis.com/css2?family=Source+Sans+3:wght@400;600&display=swap">
<style>
  :root {
    --backdrop: #2e2622;
    --navy: #1e3869;
    --navy-deep: #1b2f5e;
    --white: #ffffff;
    --teal: #6fc0d3;
    --teal-light: #bfe3ec;
    --logo-grey: #8b9094;
    --title-grey: #66696d;
    --rule: #2f4377;
  }
  * { box-sizing: border-box; margin: 0; padding: 0; }
  html, body {
    width: 1200px; height: 844px; overflow: hidden;
    background: var(--backdrop);
    font-family: "Source Sans 3", "Myriad Pro", Arial, sans-serif;
  }
  .spread {
    position: absolute; left: 24px; top: 14px;
    width: 1152px; height: 815px;
    display: flex;
  }
  .panel { position: relative; width: 576px; height: 100%; overflow: hidden; }

  /* Back panel */
  .back { background: var(--navy); }
  .back .base-rule {
    position: absolute; left: 0; right: 0; top: 790px; height: 3px; background: var(--white);
  }
  .brand { position: absolute; display: flex; align-items: center; white-space: nowrap; font-weight: 600; }
  .brand .dot { border-radius: 50%; flex: none; }
  .back .brand { left: 107px; top: 717px; gap: 17px; font-size: 32px; color: var(--white); }
  .back .brand .dot { width: 60px; height: 60px; background: var(--white); }

  /* Front panel */
  .front { background: var(--white); }
  .front .sky {
    position: absolute; left: 0; top: 0; width: 100%; height: 47px;
    background: linear-gradient(180deg, #f2f2f2, #d9dadb);
  }
  .front .masthead {
    position: absolute; left: 0; top: 47px; width: 100%; height: 153px;
    background: linear-gradient(90deg, var(--teal-light) 0%, #a5d7e3 55%, var(--teal) 100%);
  }
  .front .brand { left: 80px; top: 85px; gap: 20px; font-size: 36px; color: var(--logo-grey); }
  .front .brand .dot { width: 70px; height: 70px; background: var(--navy-deep); }
  .front .photo {
    position: absolute; left: 0; top: 200px; width: 100%; height: 303px;
    background:
      radial-gradient(ellipse at 75% 30%, #e4e4e4 0%, #a8a8a8 40%, transparent 70%),
      linear-gradient(180deg, #bdbdbd 0%, #7b7b7b 45%, #2a2a2a 80%, #111 100%);
  }
  .front .title-band {
    position: absolute; left: 71px; width: 445px; top: 564px; height: 58px;
    border-top: 1.5px solid var(--rule); border-bottom: 1.5px solid var(--rule);
    display: flex; align-items: center; padding-left: 16px;
    font-size: 25px; font-weight: 400; color: var(--title-grey);
  }
  .programs {
    position: absolute; left: 0; width: 584px; top: 688px;
    list-style: none; text-align: center;
    font-size: 18.5px; color: var(--navy); line-height: 43px;
  }
  .programs li { display: inline; }
  .programs li + li::before {
    content: ""; display: inline-block; width: 6px; height: 6px; border-radius: 50%;
    background: #9a9da1; margin: 0 21px; vertical-align: middle;
  }
  .programs .row { display: block; }
  .front .base-rule {
    position: absolute; left: 0; right: 0; top: 790px; height: 3px; background: var(--navy-deep);
  }
</style>
</head>
<body>
  <main class="spread">
    <section class="panel back">
      <div class="brand"><span class="dot"></span>Meridian Justice</div>
      <div class="base-rule"></div>
    </section>

    <section class="panel front">
      <div class="sky"></div>
      <div class="masthead"></div>
      <div class="brand"><span class="dot"></span>Meridian Justice</div>
      <div class="photo" role="img" aria-label="Black and white photo of a judge's gavel resting on its block in front of an open law book"></div>
      <h1 class="title-band">Comprehensive Offender Programs</h1>
      <div class="programs">
        <ul class="row"><li>Pre Trial</li><li>Diversion</li><li>Deferred Prosecution</li></ul>
        <ul class="row"><li>Jail Alternative</li><li>Probation</li></ul>
      </div>
      <div class="base-rule"></div>
    </section>
  </main>
</body>
</html>
```